Business Card Design - Photographer

I am a landscape photographer and I require a business card design. 

I require two designs:
1)  a double sided business card
 and
b)  a single sided business card 

The single sided design can either be the same as the double sided (with just one side having all the information)....or it can be an entire new design. Its up to you.

My corporate colours are (CMYK):

Blue   69, 32, 0, 0
Grey  72,  64,  47,  31
Green  32,  2,  91,  0
Yellow   0, 19, 92, 0
Orange  0, 39, 75, 0

Colour space in final file should be in CMYK.

The details that need to be included on the card:

- Use the provided Logo
- Name: Wiktor Baranowski
- Email:   sales@vistalumeworks.com.au
- Website:    vistalumeworks.com.au
- Twitter:    twitter.com/vistalumeworks
- Facebook:   facebook.com/vistalumeworks
- Mobile  0417 539 662

Please use the attached template to design the logo to the specified size, including the marked bleed lines. I have also attached my logo in PNG (transparent background) and ai format for you to use.

The final file should be:
- Photoshop version with layers so I can edit the name/text etc. All non vector files should be high resolution at 1039 x 697 pixels at 300 dpi.

I also require a file as:
- Vector based PDF

Anyway questions please contact me.

Thank you

Industry/Entity Type

Landscape

Logo styles of interest
Pictorial/Combination Logo
Abstract Logo
Wordmark Logo
Lettermark Logo
Requirements
Must have
• The details that need to be included on the card:

- Use the provided Logo
- Name: Wiktor Baranowski
- Email: sales@vistalumeworks.com.au
- Website: vistalumeworks.com.au
- Twitter: twitter.com/vistalumeworks
- Facebook: facebook.com/vistalumeworks
- Mobile 0417 539 662

```html
<!DOCTYPE html>
<html lang="en">
<head>
<meta charset="utf-8">
<title>Vistalume Works – Business Card</title>
<link rel="stylesheet" href="https://fonts.googleapis.com/css2?family=Cinzel:wght@500;600&family=Tinos&family=Lato:wght@400&display=swap">
<style>
  :root {
    --stage: #e9e7e3;
    --card: #ffffff;
    --ink: #3e4155;
    --band: #3f4256;
    --accent-orange: #e9a046;
    --accent-blue: #3f9bd8;
    --text: #3b3b3b;
  }
  * { margin: 0; padding: 0; box-sizing: border-box; }
  html, body { width: 1200px; height: 397px; overflow: hidden; background: var(--stage); }
  .canvas { position: relative; width: 1200px; height: 397px; }
  .card {
    position: absolute; top: 47px; width: 524px; height: 298px;
    background: var(--card); box-shadow: 0 1px 4px rgba(0,0,0,.18);
  }
  .card--front { left: 43px; }
  .card--back { left: 601px; }

  .brand { position: absolute; left: 0; right: 0; display: flex; flex-direction: column; align-items: center; }
  .brand__mark { border-radius: 50%; background: var(--ink); }
  .brand__name { font-family: "Cinzel", serif; font-weight: 600; color: var(--ink); white-space: nowrap; line-height: 1; }
  .brand__person {
    font-family: "Cinzel", serif; font-weight: 600; color: var(--ink);
    white-space: nowrap; line-height: 1; border-top: 1px solid var(--ink);
  }

  .card--front .brand { top: 28px; }
  .card--front .brand__mark { width: 76px; height: 76px; }
  .card--front .brand__name { font-size: 22px; margin-top: 6px; letter-spacing: .3px; }
  .card--front .brand__person { font-size: 8.5px; letter-spacing: 1.6px; margin-top: 4px; padding: 4px 14px 0; }

  .card--back .brand { top: 46px; }
  .card--back .brand__mark { width: 94px; height: 94px; }
  .card--back .brand__name { font-size: 33px; margin-top: 28px; letter-spacing: .5px; }
  .card--back .brand__person { font-size: 11.5px; letter-spacing: 2.4px; margin-top: 6px; padding: 6px 28px 0; }

  .rule { position: absolute; left: 0; right: 0; top: 171px; height: 2px; background: var(--accent-orange); }
  .address-band {
    position: absolute; left: 0; right: 0; top: 177px; height: 33px; background: var(--band);
    display: flex; align-items: center; justify-content: center;
    font-family: "Tinos", serif; font-size: 15px; color: #fff;
  }
  .contacts {
    position: absolute; left: 0; right: 0; top: 226px;
    font-family: "Tinos", serif; font-size: 13.5px; color: var(--text);
    display: flex; flex-direction: column; align-items: center; gap: 2px;
  }
  .contacts__row { display: flex; align-items: center; gap: 6px; line-height: 17px; }
  .contact { display: inline-flex; align-items: center; gap: 4px; }
  .contact svg { display: block; }
  .social-dot { width: 9px; height: 9px; background: var(--accent-blue); border-radius: 1px; }

  .website {
    position: absolute; left: 0; right: 0; top: 253px; text-align: center;
    font-family: "Lato", sans-serif; font-size: 13.5px; letter-spacing: 2.6px; color: var(--text);
  }
</style>
</head>
<body>
<div class="canvas">
  <section class="card card--front">
    <div class="brand">
      <div class="brand__mark"></div>
      <div class="brand__name">VISTALUME WORKS</div>
      <div class="brand__person">WIKTOR BARANOWSKI</div>
    </div>
    <div class="rule"></div>
    <div class="address-band">00, Complex Name, State Name, City 0020</div>
    <div class="contacts">
      <div class="contacts__row">
        <span class="contact">
          <svg width="7" height="10" viewBox="0 0 7 10"><rect x="0.5" y="0.5" width="6" height="9" rx="1" fill="none" stroke="#555" stroke-width="1"/><rect x="1.8" y="1.8" width="3.4" height="5" fill="#555"/></svg>
          0417 539 662
        </span>
      </div>
      <div class="contacts__row">
        <span class="contact"><span class="social-dot"></span>vistalumeworks</span>
        <span class="contact"><span class="social-dot"></span>vistalumeworks</span>
      </div>
      <div class="contacts__row">
        <span class="contact">
          <svg width="10" height="7" viewBox="0 0 10 7"><rect width="10" height="7" fill="#555"/><path d="M0 0 L5 4 L10 0" fill="none" stroke="#fff" stroke-width="1"/></svg>
          sales@vistalumeworks.com.au
        </span>
        <span class="contact">
          <svg width="9" height="9" viewBox="0 0 9 9"><circle cx="4.5" cy="4.5" r="4.5" fill="#555"/></svg>
          www.vistalumeworks.com.au
        </span>
      </div>
    </div>
  </section>

  <section class="card card--back">
    <div class="brand">
      <div class="brand__mark"></div>
      <div class="brand__name">VISTALUME WORKS</div>
      <div class="brand__person">WIKTOR BARANOWSKI</div>
    </div>
    <div class="website">www.vistalumeworks.com.au</div>
  </section>
</div>
</body>
</html>
```